Website Design for Videographer

I am looking to update my website - www.brinolvaske.com. I am a wedding videographer who specialises in natural and documentary videography.

The website will be built by my designer using the Wordpress Plinthworx framework.

Requirements;
I want the website to have a clean white look mixed in with video footage.
Needs to be classy. At the moment my website uses a lot of Gold. On the new look I DO NOT want gold.

Need a web and mobile design for the following 12 pages;

* Home page (need to have example videos and text)
* About (this is about me and my service)
* Videos (examples of my work)
* Testimonials
* Packages
* Contact
* Content (this is to show social media content that I am making in a vertical format and advertise this service).
* Blog (index page for blog)
* Blog pages (individual pages for blog content)
* Wedding Venues Index Page (https://brinolvaske.com/north-east-wedding-venues/)
* Individual venue pages (https://brinolvaske.com/north-east-wedding-venues/marlow-tendle-lodge-wedding-videos/) - Needs to show videos, photos, text as is on the current page.
* Venue Tours (https://brinolvaske.com/wedding-venue-tours/)

My current logo is attached however on the website I want to go for a black and white style for it.

Example styles I like however must not be copied.
https://joswelbrant.co.uk/about/
https://oakandripple.co.uk/ (if done in white)
https://tumblemothpictures.co.uk/

Target Market(s)

Couples getting married aged 25-35

Industry/Entity Type

Weddings

Number of Pages Required

5+ page

Font styles to use
Sans Serif

Requirements
Must have
• A classy look, black and white, use videos and photos.
Should not have
• Gold colour

```html
<!DOCTYPE html>
<html lang="en">
<head>
<meta charset="utf-8">
<title>Brin Olvaske Wedding Films – Mobile Screens</title>
<link href="https://fonts.googleapis.com/css2?family=Inter:wght@400;500;600;700;800&display=swap" rel="stylesheet">
<style>
:root{
  --ink:#111111;
  --text:#2a2a2a;
  --paper:#ffffff;
  --card:#f3f3f3;
  --frame:#cfcfcf;
  --on-dark:#ffffff;
  --on-dark-soft:#e6e6e6;
  --rule:#bdbdbd;
}
*{box-sizing:border-box;margin:0;padding:0}
html,body{width:1200px;height:920px;overflow:hidden;background:var(--paper)}
body{font-family:"Inter",Arial,sans-serif;color:var(--text)}
.stage{position:absolute;left:0;top:0;width:2190px;height:1680px;transform:scale(.5479);transform-origin:0 0;overflow:hidden}
.screen{position:absolute;top:45px;width:386px;height:1700px;border:2px solid var(--frame);border-bottom:none;background:var(--paper);overflow:hidden}
.screen--home{left:45px;height:1538px;border-bottom:2px solid var(--frame)}
.screen--story{left:475px}
.screen--videos{left:903px;height:1572px;border-bottom:2px solid var(--frame)}
.screen--kit{left:1332px}
.screen--footer{left:1761px}
.abs{position:absolute}
.center{text-align:center}
.body{font-size:14.2px;line-height:23.5px;color:var(--text)}
.body p+p{margin-top:23.5px}
.light{color:var(--on-dark-soft)}
.h-hero{font-weight:700;color:var(--on-dark);font-size:33px;line-height:38px;letter-spacing:.3px;text-transform:uppercase}
.h-section{font-weight:700;color:var(--ink);font-size:32px;line-height:38px}
.h-card{font-weight:600;color:var(--ink);font-size:20px;line-height:29.5px}
.h-item{font-weight:700;color:var(--ink);font-size:16px;line-height:25px}
.btn{background:var(--ink);color:#fff;font-weight:600;font-size:14px;display:flex;align-items:center;justify-content:center}
.media{position:absolute;overflow:hidden}
.play{position:absolute;left:50%;top:50%;width:48px;height:48px;margin:-24px 0 0 -24px;border-radius:50%;background:#fff}
.play::after{content:"";position:absolute;left:19px;top:14px;border-left:16px solid var(--ink);border-top:10px solid transparent;border-bottom:10px solid transparent}
.card{position:absolute;left:16px;width:351px;background:var(--card)}
.num{position:absolute;left:162px;width:58px;height:58px;background:var(--ink);color:#fff;font-weight:700;font-size:34px;display:flex;align-items:center;justify-content:center;border-radius:3px}
.links li{list-style:none;font-size:14.5px;line-height:28.5px;color:var(--ink)}
</style>
</head>
<body>
<div class="stage">

  <!-- Screen 1: home hero -->
  <section class="screen screen--home">
    <div class="media" style="left:0;top:0;width:382px;height:790px;background:linear-gradient(180deg,#4a4a44 0%,#3b3a33 30%,#2d2b25 60%,#0c0b0a 100%)" role="img" aria-label="Couple embracing among trees at dusk"></div>
    <div class="abs" style="left:16px;top:44px;font-size:10px;font-weight:600;letter-spacing:2px;color:#fff">BRIN OLVASKE</div>
    <svg class="abs" style="left:340px;top:38px" width="22" height="18" viewBox="0 0 22 18"><path d="M0 1h22M0 9h22M0 17h22" stroke="#fff" stroke-width="2"/></svg>
    <h1 class="abs h-hero center" style="left:0;top:352px;width:382px">North East<br>Wedding<br>Videographer</h1>
    <div class="abs center" style="left:0;top:488px;width:382px;color:#fff;font-size:17px">Brin Olvaske</div>
    <div class="media" style="left:15px;top:836px;width:351px;height:198px;background:linear-gradient(135deg,#2f3a34,#5b574d 50%,#2a2622)" role="img" aria-label="First dance video still"><span class="play"></span></div>
    <h2 class="abs h-section center" style="left:0;top:1082px;width:382px">Stunning North East<br>Wedding Films</h2>
    <div class="abs body center" style="left:14px;top:1181px;width:354px">A trusted and acclaimed North East wedding videographer who has more than 25 years of videography experience. From beautiful barns and luxurious country hotels to sun-drenched Greek Islands and ancient Italian abbeys, he has filmed all kinds of unforgettable weddings. If you’re looking for a highly experienced wedding videographer who focuses on your story, the “goosebump” moments and the emotions filling the room as you entertain your guests, then get in touch with Brin today.</div>
    <div class="abs btn" style="left:137px;top:1447px;width:108px;height:40px">Watch Films</div>
  </section>

  <!-- Screen 2: story cards -->
  <section class="screen screen--story">
    <div class="card" style="top:47px;height:613px">
      <div class="media" style="left:51px;top:24px;width:253px;height:315px;background:linear-gradient(135deg,#c9a94e,#e2c878 45%,#b8953d)" role="img" aria-label="Wedding awards 2024 winner certificate"></div>
      <h3 class="abs h-card center" style="left:0;top:354px;width:351px">Vowline Wedding Awards<br>2024 Winner</h3>
      <div class="abs body center" style="left:20px;top:424px;width:311px">I’m honoured to have been the only wedding videographer from the North East to win the Vowline Wedding Awards 2024. It’s evidence of the incredible moments I’ve recorded for couples on their wedding day. This award was their satisfaction and the memories we’ve made together.</div>
    </div>
    <div class="card" style="top:675px;height:564px">
      <div class="media" style="left:16px;top:16px;width:319px;height:179px;background:linear-gradient(135deg,#bfb8a6,#e8e2d4 50%,#6d6255)" role="img" aria-label="Couple with horses video still"><span class="play"></span></div>
      <h3 class="abs h-card center" style="left:0;top:210px;width:351px">Wedding Videography For<br>Natural Moments</h3>
      <div class="abs body center" style="left:20px;top:281px;width:311px">My approach to wedding videography is straightforward: I let you and your guests enjoy the pleasure, love, and festivities of the day. The focus will be on capturing the spontaneous, real interactions that make your wedding so unique. When you look back on your wedding day, I want you to remember the genuine smiles, genuine laughing, and spontaneous moments of emotion that you might have missed in the flurry of events.</div>
    </div>
    <div class="card" style="top:1254px;height:400px">
      <div class="media" style="left:16px;top:16px;width:319px;height:180px;background:linear-gradient(135deg,#d9dcdf,#c95a63 55%,#5b6d78)" role="img" aria-label="Poolside ceremony with balloons video still"><span class="play"></span></div>
      <h3 class="abs h-card center" style="left:0;top:211px;width:351px">Relive Those Wedding<br>Moments Over And Over Again</h3>
      <div class="abs body center" style="left:20px;top:281px;width:311px">The nicest part of being a videographer is hearing about the emotional impact of my wedding videos on couples. Your wedding day goes by so quickly, and there are</div>
    </div>
  </section>

  <!-- Screen 3: videos -->
  <section class="screen screen--videos">
    <div class="media" style="left:0;top:0;width:382px;height:655px;background:linear-gradient(180deg,#3e3b37,#6a5d4f 45%,#33362d)" role="img" aria-label="Couple at sunset"></div>
    <h2 class="abs h-hero center" style="left:10px;top:50px;width:362px;font-size:32px;line-height:38.5px">Your wedding day is the most important day of your life…</h2>
    <div class="abs body center light" style="left:14px;top:233px;width:354px">
      <p>The celebration of your love story… and you’ll want to remember it for the rest of your lives.</p>
      <p>Your wedding film is the best way to keep this day alive forever … a newlywed’s gift that keeps giving … an infinite reminder of those special moments and memories.</p>
      <p>Everything about your wedding day belongs to you, the couple. Your story. Your vibe. Your friends and family. Your pre-wedding jitters. Your tears. Your laughter. Your vows. Your excitement. Your first dance. Everything. And I’m passionate about creating a wedding film that captures the very essence of your day and turning it into a family heirloom you’ll treasure forever.</p>
    </div>
    <h2 class="abs h-section center" style="left:0;top:702px;width:382px;letter-spacing:.5px">WEDDING VIDEOS</h2>
    <div class="media" style="left:15px;top:763px;width:351px;height:200px;background:linear-gradient(135deg,#1e2433,#4a3e3a 55%,#1a1c26)" role="img" aria-label="Sparkler send-off video still"><span class="play"></span></div>
    <div class="abs center h-item" style="left:0;top:977px;width:382px">Durham Celebration</div>
    <svg class="abs" style="left:136px;top:1022px" width="110" height="30" viewBox="0 0 110 30"><path d="M14 3 3 15l11 12M96 3l11 12-11 12" fill="none" stroke="#111" stroke-width="3"/></svg>
    <div class="abs btn" style="left:131px;top:1083px;width:121px;height:40px">View All Films</div>
    <div class="media" style="left:0;top:1170px;width:382px;height:400px;background:linear-gradient(180deg,#5b5d55,#3d4236 60%,#2b2e27)" role="img" aria-label="Wedding guests outdoors"></div>
    <h2 class="abs h-hero center" style="left:0;top:1217px;width:382px;font-size:32px">Amazing Weddings</h2>
    <div class="abs body center light" style="left:14px;top:1287px;width:354px">But the video isn’t just for you. Imagine your grandchildren opening that digital file a century from now to learn about the beautiful day that started their family tree. It’s more than simply a video; it’s a family heritage that will be treasured for decades. How valuable is that? Knowing that the happiest day of your life will live on forever, and that all of your emotions, smiles, and tears will be felt by future generations. When you think about it, it’s simply breath taking.</div>
  </section>

  <!-- Screen 4: kit -->
  <section class="screen screen--kit">
    <div class="num" style="top:47px">1</div>
    <div class="media" style="left:107px;top:129px;width:168px;height:168px;border-radius:6px;background:linear-gradient(135deg,#b7a58b,#5d5650 50%,#a8977e)" role="img" aria-label="Camera kit laid out flat"></div>
    <h3 class="abs h-item center" style="left:0;top:322px;width:382px">Documentary-Style Filming</h3>
    <div class="abs body center" style="left:22px;top:358px;width:338px">Being a wedding videographer entails more than simply pushing the record button; it also entails employing the correct gear to capture every beautiful moment. Let’s face it, I’m a bit of a gearhead. I enjoy experimenting with new videography technology, but don’t worry, I keep things low-key on your wedding day. It’s all about recording those candid, documentary-style moments that distinguish your wedding.</div>
    <div class="num" style="top:616px">2</div>
    <div class="media" style="left:107px;top:698px;width:168px;height:168px;border-radius:6px;background:linear-gradient(135deg,#dde2e8,#9aa3ad 55%,#4e5660)" role="img" aria-label="Camera drone close-up"></div>
    <h3 class="abs h-item center" style="left:0;top:890px;width:382px">Aerial Views and Smooth Shots</h3>
    <div class="abs body center" style="left:22px;top:927px;width:338px">When it comes to equipment, I’m talking about top-tier stuff. Consider aerial photography. I have a Skyrise Aero 3 Pro drone that provides me with breathtaking bird’s-eye views of your site and celebrations. I also have a Skyrise Lite 2 on standby as a backup. To guarantee that everything is caught smoothly, I occasionally utilise a gimbal, especially during critical occasions like your first dance.</div>
    <div class="num" style="top:1185px">3</div>
    <div class="media" style="left:107px;top:1267px;width:168px;height:168px;border-radius:6px;background:linear-gradient(135deg,#7a4a2e,#2a2220 50%,#5a3522)" role="img" aria-label="Audio recorder on wooden table"></div>
    <h3 class="abs h-item center" style="left:20px;top:1459px;width:342px">Capturing Every Moment, Sight, and Sound</h3>
    <div class="abs body center" style="left:22px;top:1521px;width:338px">But what good is a wedding film without the ceremony and speeches? I go all out for those crucial moments, filming with at least three Norvik cameras for a multi-camera edit. The goal is to maintain the spotlight on you</div>
  </section>

  <!-- Screen 5: north east + footer -->
  <section class="screen screen--footer">
    <div class="media" style="left:0;top:0;width:382px;height:790px;background:linear-gradient(180deg,#4c5a62,#33474a 40%,#243430 75%,#1b2624)" role="img" aria-label="North East coastline"></div>
    <h2 class="abs h-hero center" style="left:0;top:50px;width:382px;font-size:32px">I love the North<br>East</h2>
    <div class="abs body center light" style="left:14px;top:156px;width:354px">
      <p>The North East isn’t just a place on the map for me; it’s a canvas where love stories come to life. And that’s where my videography skills come into play. Think about it, we’ve got everything from historic Durham Cathedral to the iconic Tyne Bridge as backdrops. Plus, there’s something magical about North East weddings, whether it’s a rustic affair in a barn or an elegant ceremony in a county house.</p>
      <p>Of course, the real magic happens when I get to combine my love for the North East with my passion for filming weddings. The rich history of Durham, the vibrant culture of Newcastle, and the stunning beaches of Northumberland add layers to each wedding video I produce. It’s like making a mini-movie where every scene is filled with genuine emotion and the setting is as iconic as it gets.</p>
      <p>So, yeah, being a North East wedding videographer is more than a job for me; it’s a way of life. I wouldn’t trade it for anything else. Because, at the end of the day, I’m doing what I love in a place that I love, while helping people relive the most incredible day of their lives. Does it get any better than that? I don’t think so.</p>
    </div>
    <div class="abs center" style="left:0;top:890px;width:382px;font-size:15px;font-weight:600;letter-spacing:4px;color:var(--ink)">BRIN OLVASKE</div>
    <span class="abs" style="left:117px;top:951px;width:24px;height:24px;border-radius:50%;background:var(--ink)" aria-label="Social profile"></span>
    <span class="abs" style="left:179px;top:951px;width:24px;height:24px;border-radius:50%;background:var(--ink)" aria-label="Social profile"></span>
    <span class="abs" style="left:242px;top:951px;width:24px;height:24px;border-radius:50%;background:var(--ink)" aria-label="Social profile"></span>
    <div class="abs center h-item" style="left:0;top:1004px;width:382px">CONTACT</div>
    <svg class="abs" style="left:16px;top:1041px" width="16" height="16" viewBox="0 0 16 16"><path d="M3 1h3l1.5 4-2 1.2a9 9 0 0 0 4.3 4.3L11 8.5l4 1.5v3a2 2 0 0 1-2 2A12 12 0 0 1 1 3a2 2 0 0 1 2-2z" fill="none" stroke="#111" stroke-width="1.2"/></svg>
    <div class="abs" style="left:42px;top:1039px;font-size:14.5px;color:var(--ink)">07700 900 318</div>
    <svg class="abs" style="left:16px;top:1071px" width="16" height="12" viewBox="0 0 16 12"><rect x=".6" y=".6" width="14.8" height="10.8" fill="none" stroke="#111" stroke-width="1.2"/><path d="M1 1l7 6 7-6" fill="none" stroke="#111" stroke-width="1.2"/></svg>
    <div class="abs" style="left:42px;top:1067px;font-size:14.5px;color:var(--ink)">films@brinolvaske.com</div>
    <div class="abs" style="left:16px;top:1108px;width:258px;height:58px;border:1.5px solid #999;border-radius:5px" aria-label="Renewable energy badge"></div>
    <div class="abs center h-item" style="left:0;top:1190px;width:382px">LINKS</div>
    <ul class="abs links" style="left:16px;top:1222px">
      <li>FAQ’s</li><li>Commercial Videography</li><li>Free Speeches Guide</li><li>Blog</li><li>Iso Island Weddings</li><li>Lake District Wedding Videos</li><li>North East Wedding Venues</li><li>Newcastle Wedding Videographer</li><li>Northumberland Wedding Videos</li><li>North Yorkshire Weddings</li><li>Wedding Venue Tours</li><li>Durham Wedding Videographer</li>
    </ul>
    <div class="abs" style="left:16px;top:1579px;width:350px;height:1px;background:var(--rule)"></div>
    <div class="abs center" style="left:0;top:1607px;width:382px;font-size:15.5px;font-weight:500;color:var(--ink)">COPYRIGHT 2010 - 2024 © BRIN OLVASKE</div>
  </section>

</div>
</body>
</html>
```